Automotive Accessories Business Card

Design a business template that match our new logo design and our industry.

https://www.qelmotorgear.com/

Target Market(s)

Aftermarket auto parts and accessories

Industry/Entity Type

automotive

Contact Information for Business Card

company logo

Font styles to use
Serif
Sans Serif

Colors
EB3D1F
EC4F4E
F09395
F8D3D4
FCEDEE

```html
<!DOCTYPE html>
<html lang="en">
<head>
<meta charset="utf-8">
<title>QEL Motor Gear – Business Card</title>
<link href="https://fonts.googleapis.com/css2?family=Montserrat:wght@400;500;700;800&display=swap" rel="stylesheet">
<style>
  :root {
    --brand-red: #d71f26;
    --brand-red-soft: #e0474d;
    --ink-dark: #3a3a3c;
    --ink-grey: #5a5a5c;
    --paper: #ffffff;
    --backdrop: #e9e9ea;
  }
  * { margin: 0; padding: 0; box-sizing: border-box; }
  html, body {
    width: 1200px; height: 802px; overflow: hidden;
    background: var(--backdrop);
    font-family: "Montserrat", sans-serif;
  }
  .sheet {
    width: 1200px; height: 802px;
    display: flex; align-items: center; justify-content: center; gap: 56px;
  }
  .card {
    position: relative;
    width: 530px; height: 303px;
    overflow: hidden;
    box-shadow: 0 8px 24px rgba(0,0,0,.12);
  }
  /* Front */
  .card-front { background: var(--paper); border-bottom: 6px solid var(--brand-red); }
  .card-front .edge-band {
    position: absolute; right: 0; top: 0; width: 12px; height: 100%;
    background: linear-gradient(var(--ink-dark) 62%, var(--brand-red) 62%);
  }
  .card-front .faint-name {
    position: absolute; right: 40px; bottom: 24px;
    font-weight: 800; font-size: 92px; letter-spacing: -2px;
    color: var(--brand-red); opacity: .07;
  }
  .brand-lockup {
    position: absolute; left: 44px; top: 54px;
    display: flex; align-items: center; gap: 12px;
  }
  .brand-mark { width: 22px; height: 22px; background: var(--brand-red); }
  .brand-name {
    font-weight: 800; font-size: 26px; letter-spacing: .5px;
    color: var(--ink-dark); line-height: 1;
  }
  .address {
    position: absolute; right: 40px; top: 40px;
    text-align: right; font-size: 13px; line-height: 1.45; color: var(--ink-grey);
  }
  .person { position: absolute; left: 44px; top: 150px; }
  .person-name {
    font-weight: 700; font-size: 19px; letter-spacing: 2px;
    color: var(--brand-red); text-transform: uppercase;
  }
  .person-title { font-size: 13px; color: var(--ink-grey); margin-top: 2px; }
  .contact-list { list-style: none; margin-top: 16px; }
  .contact-list li {
    display: flex; align-items: center; gap: 10px;
    font-size: 13.5px; color: var(--ink-grey); line-height: 1.65;
  }
  .contact-list svg { width: 12px; height: 12px; fill: var(--brand-red); flex: none; }

  /* Back */
  .card-back { background: var(--brand-red); }
  .card-back .faint-name {
    position: absolute; left: 20px; bottom: -30px;
    font-weight: 800; font-size: 190px; letter-spacing: -6px;
    color: var(--brand-red-soft); opacity: .7;
  }
  .card-back .brand-lockup {
    left: 50%; top: 50%; transform: translate(-50%, -50%);
  }
  .card-back .brand-mark { background: var(--paper); width: 28px; height: 28px; }
  .card-back .brand-name { color: var(--paper); font-size: 32px; }
</style>
</head>
<body>
<main class="sheet">
  <section class="card card-front">
    <div class="faint-name" aria-hidden="true">QEL</div>
    <div class="edge-band"></div>
    <div class="brand-lockup">
      <span class="brand-mark"></span>
      <span class="brand-name">QEL MOTOR GEAR INC</span>
    </div>
    <address class="address">
      240 W. Harbor Ave.<br>Suite B<br>Riverside, CA 92501
    </address>
    <div class="person">
      <p class="person-name">Daniel Reyes</p>
      <p class="person-title">Manager</p>
      <ul class="contact-list">
        <li><svg viewBox="0 0 24 24"><path d="M6.6 10.8a15.1 15.1 0 0 0 6.6 6.6l2.2-2.2c.3-.3.7-.4 1-.2 1.1.4 2.3.6 3.6.6.6 0 1 .4 1 1V20c0 .6-.4 1-1 1A17 17 0 0 1 3 4c0-.6.4-1 1-1h3.5c.6 0 1 .4 1 1 0 1.3.2 2.5.6 3.6.1.3 0 .7-.2 1z"/></svg>1-866-555-0142</li>
        <li><svg viewBox="0 0 24 24"><path d="M2 5h20v14H2zm2 2v.5l8 5 8-5V7z"/></svg>sales@qelmotorgear.com</li>
        <li><svg viewBox="0 0 24 24"><circle cx="12" cy="12" r="10"/></svg>www.qelmotorgear.com</li>
      </ul>
    </div>
  </section>

  <section class="card card-back">
    <div class="faint-name" aria-hidden="true">QEL</div>
    <div class="brand-lockup">
      <span class="brand-mark"></span>
      <span class="brand-name">QEL MOTOR GEAR INC</span>
    </div>
  </section>
</main>
</body>
</html>
```